Business Card for a Jewellery Brand

Business card for an upscale jewellery brand. Attached is the brand logo and icon and color board. I am looking for two card versions: one for the founder and one is generic. The card should be elegant and convey upscale and premium feel. I am open to both square and rectangle card shapes.

Industry/Entity Type

Jewelry

Contact Information for Business Card

Two cards: (1) Sunela Parvaniya (Founder) (2) General
(1) Sunela Parvaniya card should have Name: Sunela Parvaniya, Title: Founder Email id: sunela@quiremo.com.au. Phone no: +61452913307
(2) Generic card should have Email id: info@quiremo.com.au. Phone no: +61436207518

Requirements
Must have
• Workmark
• ICON
• Phone no
• Email ID
• ABN: 58219740312 (Note: ABN is Business number in Australia)
• Website: www.quiremo.com.au
• Instagram: quiremo_jewellery
• Facebook: @quiremojewellery
Nice to have
• Tagline

```html
<!DOCTYPE html>
<html lang="en">
<head>
<meta charset="utf-8">
<title>Quiremo Business Cards</title>
<link rel="stylesheet" href="https://fonts.googleapis.com/css2?family=Source+Sans+3:wght@400;600&display=swap">
<style>
  :root {
    --stage: #000000;
    --card: #323336;
    --rose: #e9a39c;
    --ink: #ececec;
    --rule: rgba(255, 255, 255, 0.08);
    --font: "Source Sans 3", "Myriad Pro", Arial, sans-serif;
  }
  * { margin: 0; padding: 0; box-sizing: border-box; }
  html, body {
    width: 1200px;
    height: 900px;
    overflow: hidden;
    background: var(--stage);
    font-family: var(--font);
  }
  .stage { position: relative; width: 1200px; height: 900px; }

  .card {
    position: absolute;
    top: 271px;
    width: 457px;
    height: 281px;
    background: var(--card);
    border-radius: 14px;
  }
  .card--front { left: 137px; }
  .card--back { left: 626px; }

  /* Front: brand name block */
  .front-brand {
    position: absolute;
    left: 40px;
    top: 104px;
    width: 170px;
    text-align: center;
    color: var(--rose);
    font-size: 26px;
    font-weight: 400;
    letter-spacing: 0.18em;
    padding-left: 0.18em;
    line-height: 30px;
  }
  .front-brand .brand-dot {
    display: block;
    width: 16px;
    height: 16px;
    margin: 0 auto 14px;
    border: 2px solid var(--rose);
    border-radius: 50%;
  }
  .divider {
    position: absolute;
    left: 224px;
    top: 80px;
    width: 1px;
    height: 120px;
    background: var(--rule);
  }

  /* Front: details */
  .details {
    position: absolute;
    left: 250px;
    top: 60px;
    color: var(--ink);
  }
  .holder-name {
    color: var(--rose);
    font-size: 17px;
    font-weight: 600;
    line-height: 20px;
  }
  .holder-title { font-size: 13px; line-height: 15px; }
  .abn {
    margin-top: 15px;
    font-size: 13px;
    line-height: 18px;
  }
  .abn-label { color: var(--rose); font-weight: 600; font-size: 14px; }
  .contact-list { list-style: none; margin-top: 12px; }
  .contact-list li {
    display: flex;
    align-items: center;
    height: 19.3px;
    font-size: 13px;
  }
  .contact-icon {
    width: 11px;
    height: 11px;
    margin-right: 6px;
    flex: none;
    fill: var(--rose);
  }
  .social-dot {
    width: 10px;
    height: 10px;
    margin: 0 7px 0 1px;
    border-radius: 50%;
    background: var(--rose);
    flex: none;
  }

  /* Back: centred brand */
  .back-brand {
    position: absolute;
    left: 0;
    right: 0;
    top: 80px;
    text-align: center;
    color: var(--rose);
  }
  .back-brand .brand-dot {
    display: block;
    width: 34px;
    height: 34px;
    margin: 0 auto 22px;
    border: 3px solid var(--rose);
    border-radius: 50%;
  }
  .back-brand .wordmark {
    font-size: 38px;
    font-weight: 400;
    letter-spacing: 0.3em;
    padding-left: 0.3em;
    line-height: 44px;
  }
</style>
</head>
<body>
<main class="stage">

  <section class="card card--front" aria-label="Founder card">
    <div class="front-brand"><span class="brand-dot"></span>QUIREMO</div>
    <span class="divider"></span>
    <div class="details">
      <p class="holder-name">Sunela Parvaniya</p>
      <p class="holder-title">Founder</p>
      <p class="abn"><span class="abn-label">ABN:</span> 58219740312</p>
      <ul class="contact-list">
        <li>
          <svg class="contact-icon" viewBox="0 0 24 24" aria-hidden="true"><path d="M6.6 10.8a15.1 15.1 0 0 0 6.6 6.6l2.2-2.2c.3-.3.7-.4 1-.2 1.1.4 2.3.6 3.6.6.6 0 1 .4 1 1V20c0 .6-.4 1-1 1A17 17 0 0 1 3 4c0-.6.4-1 1-1h3.5c.6 0 1 .4 1 1 0 1.3.2 2.5.6 3.6.1.3 0 .7-.2 1z"/></svg>
          +61452913307
        </li>
        <li>
          <svg class="contact-icon" viewBox="0 0 24 24" aria-hidden="true"><path d="M2 5h20v14H2z M3.5 6.5 12 12.5l8.5-6v-.5h-17z" fill-rule="evenodd"/><path d="M2 5h20l-10 7z" opacity="0.6"/></svg>
          sunela@quiremo.com.au
        </li>
        <li>
          <svg class="contact-icon" viewBox="0 0 24 24" aria-hidden="true"><path d="M12 2a10 10 0 1 0 0 20 10 10 0 0 0 0-20zm-1 17.9A8 8 0 0 1 4.1 10L9 15v1a2 2 0 0 0 2 2zm6.9-2.5A2 2 0 0 0 16 16h-1v-3a1 1 0 0 0-1-1H8v-2h2a1 1 0 0 0 1-1V7h2a2 2 0 0 0 2-2v-.4a8 8 0 0 1 2.9 12.8z"/></svg>
          www.quiremo.com.au
        </li>
        <li><span class="social-dot"></span>quiremo_jewellery</li>
        <li><span class="social-dot"></span>@quiremojewellery</li>
      </ul>
    </div>
  </section>

  <section class="card card--back" aria-label="Brand card">
    <div class="back-brand">
      <span class="brand-dot"></span>
      <p class="wordmark">QUIREMO</p>
    </div>
  </section>

</main>
</body>
</html>
```